Business Card Design

New business card design

Target Market(s)

Residential & Commercial Property Managers

Industry/Entity Type

Plumbing Services

Contact Information for Business Card

Name - Rowan Keddle, title - Director, Phone Number - 0431 286 517, email - rowan@tbk-plumbing.com.au, Company ABN - 73 215 904 386,

Font styles to use
Sans Serif

Colors
0054AA
0677BA
7BADD7
CADEEF
E8F1F8

```html
<!DOCTYPE html>
<html lang="en">
<head>
<meta charset="utf-8">
<title>TBK Plumbing Services – Business Card</title>
<link rel="stylesheet" href="https://fonts.googleapis.com/css2?family=Poppins:wght@400;500;600&display=swap">
<style>
  :root {
    --backdrop: #222222;
    --card: #ffffff;
    --navy: #1b2530;
    --blue: #29abe2;
    --taupe: #736a60;
    --ink: #1a1a1a;
  }
  * { box-sizing: border-box; margin: 0; padding: 0; }
  html, body { width: 1200px; height: 711px; overflow: hidden; background: var(--backdrop); }
  body { font-family: "Poppins", sans-serif; position: relative; }

  .card {
    position: absolute;
    width: 540px;
    height: 310px;
    background: var(--card);
    top: 200px;
    overflow: hidden;
    box-shadow: 0 10px 30px rgba(0,0,0,.55);
  }
  .card--front { left: 40px; }
  .card--back { left: 620px; }

  /* wordmark */
  .wordmark { position: absolute; display: flex; flex-direction: column; align-items: center; }
  .wordmark__row { display: flex; align-items: center; gap: 10px; }
  .wordmark__name { color: var(--navy); font-weight: 500; line-height: 1; letter-spacing: 2px; }
  .wordmark__dot { background: var(--blue); border-radius: 50%; }
  .wordmark__tag { color: var(--taupe); font-weight: 400; text-transform: lowercase; }

  .card--front .wordmark { left: 0; right: 0; top: 70px; }
  .card--front .wordmark__name { font-size: 120px; }
  .card--front .wordmark__dot { width: 22px; height: 22px; margin-top: 40px; }
  .card--front .wordmark__tag { font-size: 15px; letter-spacing: 10px; margin-top: 14px; padding-left: 10px; }

  .card--back .wordmark { left: 20px; width: 240px; top: 80px; }
  .card--back .wordmark__name { font-size: 70px; }
  .card--back .wordmark__dot { width: 14px; height: 14px; margin-top: 24px; }
  .card--back .wordmark__tag { font-size: 9px; letter-spacing: 6px; margin-top: 8px; padding-left: 6px; }

  .divider { position: absolute; left: 276px; top: 62px; width: 1px; height: 150px; background: var(--blue); }

  .contact { position: absolute; left: 300px; top: 56px; }
  .contact__name { font-size: 25px; line-height: 1.1; color: var(--taupe); font-weight: 400; }
  .contact__first { color: var(--blue); font-weight: 600; }
  .contact__title { font-size: 12px; font-weight: 500; color: var(--ink); margin-top: 2px; }
  .contact__list { list-style: none; margin-top: 18px; }
  .contact__item { display: flex; align-items: center; gap: 8px; font-size: 11.5px; color: var(--ink); line-height: 1.9; }
  .contact__icon { width: 13px; height: 13px; flex: none; }

  .band { position: absolute; left: 0; top: 252px; width: 440px; height: 24px; background: var(--blue); }
  .band__abn { position: absolute; right: 40px; top: 0; line-height: 24px; color: #fff; font-size: 11px; letter-spacing: .5px; }
  .band__end { position: absolute; left: 424px; top: 236px; width: 46px; height: 46px; border-radius: 50%; background: var(--blue); }
  .accent { position: absolute; left: 470px; top: 240px; width: 70px; height: 20px; background: var(--taupe); }
</style>
</head>
<body>
  <section class="card card--front" aria-label="Card front">
    <div class="wordmark">
      <div class="wordmark__row">
        <span class="wordmark__name">tbk</span>
        <span class="wordmark__dot"></span>
      </div>
      <span class="wordmark__tag">plumbing services</span>
    </div>
  </section>

  <section class="card card--back" aria-label="Card back">
    <div class="wordmark">
      <div class="wordmark__row">
        <span class="wordmark__name">tbk</span>
        <span class="wordmark__dot"></span>
      </div>
      <span class="wordmark__tag">plumbing services</span>
    </div>

    <div class="divider"></div>

    <div class="contact">
      <p class="contact__name"><span class="contact__first">Rowan</span> Keddle</p>
      <p class="contact__title">Director</p>
      <ul class="contact__list">
        <li class="contact__item">
          <svg class="contact__icon" viewBox="0 0 24 24" aria-hidden="true"><path fill="#29abe2" d="M6.6 10.8a15 15 0 0 0 6.6 6.6l2.2-2.2a1 1 0 0 1 1-.25 11.4 11.4 0 0 0 3.6.57 1 1 0 0 1 1 1V20a1 1 0 0 1-1 1A17 17 0 0 1 3 4a1 1 0 0 1 1-1h3.5a1 1 0 0 1 1 1c0 1.25.2 2.45.57 3.57a1 1 0 0 1-.25 1z"/></svg>
          0431 286 517
        </li>
        <li class="contact__item">
          <svg class="contact__icon" viewBox="0 0 24 24" aria-hidden="true"><circle cx="12" cy="12" r="10" fill="#29abe2"/><path d="M2 12h20M12 2c3 3 3 17 0 20M12 2c-3 3-3 17 0 20" stroke="#fff" stroke-width="1.5" fill="none"/></svg>
          www.tbk-plumbing.com.au
        </li>
        <li class="contact__item">
          <svg class="contact__icon" viewBox="0 0 24 24" aria-hidden="true"><rect x="2" y="5" width="20" height="14" rx="2" fill="#29abe2"/><path d="M3 6l9 7 9-7" stroke="#fff" stroke-width="1.6" fill="none"/></svg>
          rowan@tbk-plumbing.com.au
        </li>
      </ul>
    </div>

    <div class="accent"></div>
    <div class="band"><span class="band__abn">ABN - 73 215 904 386</span></div>
    <div class="band__end"></div>
  </section>
</body>
</html>
```